Wordpress Theme for Medical Clinics

** Please view updated Sitemap2.pdf doc to clarify some confusion ***

This is a multiuser WordPress subscription site for medical clinics. Please see attachment for sitemap. Please do not include extra content like social media icons, search bars, or images. If you have questions, please ask for clarification.
The site contains the following pages and sub-pages:

1. Home
2. Our Clinic
2a. Our Clinic > Mission
2b. Our Clinic > Services
2c. Our Clinic > Clinic Policies
2d. Our Clinic > Schedules
3. Our Staff
3a. Our Staff > [Staff member page]
4. Resources
4a. Resources > Patient Health (index)
4b. Resources > Patient Health (index) > [post]
4c. Resources > Links
4d. Resources > Forms
5. Alerts
5a. Alerts > [Alert Page]
6. Contact Us

Includes the Following Pages, Subpages, and Content
1. Home
a. About Us
b. Our Staff
c. Bulletins
d. Accepting New Patients (shown as an alert widget)
e. Links
i. Physician Toolbox
ii. Book an Appointment
f. Clinic Policies
i. Show first 3 policies (e.g. Late Arrivals, Missed Appointments, Fees)
ii. Link to Clinic Policies page
g. Primary widget (displayed on all pages)
i. Hours of operation
ii. Contact Info
1. Tel
2. Fax
3. Email
4. Address
5. Get directions (link to Google Maps)
2. Our Clinic
a. Main Page
i. Clinic Name
ii. Overview
iii. Languages Spoken
iv. Secondary Navigation
1. Mission
2. Services
3. Clinic Policies
4. Schedules (see attachment)
b. Our Clinic > Mission
c. Our Clinic > Services
i. For each service include service TITLE and DESCRIPTION
d. Our Clinic > Clinic Policies
i. For each policy include policy TITLE and DESCRIPTION
ii. Include the following policies in mockup
1. Late arrivals
2. Missed appointments
3. Fees for missed appointments
4. Referrals and follow-ups
5. Services not covered by RDA
6. Information for LTF patients
7. Medical Legal Reports
e. Our Clinic > Schedules
3. Our Staff
a. Main Page
i. Display a list of staff members. Include NAME and DESIGNATION
b. Our Staff > [Staff Name]
i. Include NAME, PICTURE, DESIGNATION, and BIO
4. Resources
a. Resources > Patient Health
i. Main Page
1. Posts (ordered by date)
a. Title
b. Summary
2. Side Navigation
a. Post Categories
ii. Patient Health > [post title]
1. Title
2. Post Category
3. Date
4. Author
5. Summary
6. Body
b. Resources > Links
1. Secondary Navigation - Categories
a. Sample Categories:
i. Local Services
ii. RDA and Drug Coverage
iii. Mental Health Resources
2. Category page
a. Include the following links in the 'Local Services' category
i. Hypertension clinics
ii. Home Care services
iii. Vaccine Clinics
c. Resources > Forms
i. Display a table with form TITLE and CATEGORY
ii. Side Navigation
1. Form Categories
a. Use the following sample Categories
i. Referrals
ii. Insurance
iii. Intake
iv. Discharge
v. Waivers
5. Alerts
a. Main page
i. List of all Alert posts
1. Include post TITLE as a link to the post
ii. Side Navigation
1. Alerts Archive
a. shown as Month + Number of posts
iii. Alerts > [Alert page]
1. Include TITLE, DATE, AUTHOR, BODY
6. Contact Us
a. Map
b. Hours of operation
c. Address
d. Phone number
e. Fax number
e. Fax number
f. Map
g. Email

Design notes:
- fixed width
- responsive (need designs for mobile, tablet, and desktop)
- simple, dark font, white background
- use Font Awesome icons where needed
- user adds own logo

Target Market(s)

Medical Clinics

Industry/Entity Type

Medical

Number of Pages Required

5+ page

Font styles to use
Serif
Sans Serif

Requirements
Must have
• Please keep designs very simple.
• Examples:
• https://www.quolbin.com/install
• http://www.ventrohax.com/company/about-us
• http://brindlequota.org/
• http://www.trosk.com/
Should not have
• Minimal or no use of shadows and gradients

```html
<!DOCTYPE html>
<html lang="en">
<head>
<meta charset="utf-8">
<title>LTF Health Centre – Our Staff</title>
<link rel="stylesheet" href="https://fonts.googleapis.com/css2?family=Lato:ital,wght@0,400;0,700;1,400&display=swap">
<style>
:root{
  --blue:#4bbad9;
  --blue-dark:#2f9ab8;
  --blue-pale:#c5e7f3;
  --ink:#222;
  --text:#666;
  --muted:#999;
  --line:#e2e2e2;
  --band:#eeeeee;
  --bg:#f2f2f2;
  --white:#fff;
}
*{box-sizing:border-box;margin:0;padding:0}
html,body{width:738px;height:1200px;overflow:hidden}
body{background:var(--bg);font-family:'Lato',sans-serif;color:var(--text);font-size:6.5px;line-height:1.6;position:relative}
a{color:var(--blue);text-decoration:none}
.abs{position:absolute}
.topbar{left:96px;top:6px;width:546px;height:14px;font-size:6.8px;display:flex;align-items:center}
.topbar .phone{color:var(--ink);display:flex;align-items:center;gap:4px}
.topbar .sep{width:1px;height:9px;background:#ccc;margin:0 8px}
.topbar .right{margin-left:auto;display:flex;gap:16px}
.sheet{left:92px;top:23px;width:553px;height:972px;background:var(--white);border-radius:3px}
.brand{left:130px;top:35px}
.brand .name{font-size:12px;font-weight:400;color:var(--ink)}
.brand .tag{font-size:5.5px;color:var(--muted);margin-top:1px}
.nav{top:36px;left:326px;display:flex;font-size:6.3px;color:var(--ink);text-transform:uppercase}
.nav span{padding:5px 8px;height:17px}
.nav .on{background:var(--blue);color:#fff;border-top:2px solid var(--blue-dark);padding-top:3px}
.rule{left:92px;top:71px;width:553px;height:2px;background:var(--blue)}
.crumbband{left:92px;top:73px;width:553px;height:31px;background:var(--band)}
.crumbband h1{position:absolute;left:40px;top:3px;font-size:10px;color:var(--blue);font-weight:700}
.crumbband p{position:absolute;left:40px;top:15px;font-size:6px;color:var(--text)}
h2{position:absolute;font-size:11px;color:var(--ink);font-weight:700}
h3{position:absolute;font-size:9px;color:var(--ink);font-weight:700}
.search{left:485px;top:117px;width:129px;height:18px;border:1px solid var(--line);display:flex}
.search span{flex:1;padding:4px 5px;font-size:6px;color:var(--muted)}
.search i{width:24px;background:var(--blue);display:flex;align-items:center;justify-content:center}
.avatar{border-radius:50%;background:var(--blue);border:2px solid var(--blue-dark)}
.card .bar{height:18px;background:var(--band);display:flex;align-items:center;font-size:6.3px;color:var(--ink)}
.card .bar b{margin-left:6px}
.card .bar em{margin-left:auto;margin-right:5px;color:var(--muted)}
.card .bar .deg{color:var(--muted);font-weight:400}
.ico{width:18px;height:18px;background:var(--blue);display:flex;align-items:center;justify-content:center}
.card p{margin-top:6px}
.card hr{border:0;border-top:1px solid var(--line);margin:6px 0 4px}
.card .spec{font-style:italic;color:var(--muted)}
.card .mail{color:var(--ink)}
.divider{left:128px;width:488px;height:4px;background:var(--band)}
table{position:absolute;left:129px;top:627px;width:488px;border-collapse:collapse;font-size:6.3px}
th{background:var(--band);height:22px;text-align:left;color:var(--ink);font-weight:700;padding-left:7px}
td{height:22.5px;padding-left:7px;color:var(--ink);border-top:1px solid #ececec}
tbody tr:nth-child(odd){background:#f6f6f6}
td.doc{color:var(--blue)}
td.doc svg{vertical-align:-1px;margin-right:3px}
.fix{display:inline-block;border:1px solid var(--blue);color:var(--blue);font-size:5px;line-height:1;padding:3px 4px;background:#fff}
.note{left:129px;top:909px;font-size:5.3px;color:var(--text)}
.note b{color:var(--ink)}
.blurb{left:128px;top:930px;width:135px;font-size:6.5px}
.cta{left:266px;top:928px;width:350px;height:51px}
.cta p{position:absolute;left:10px;top:11px;width:235px;font-size:7.5px;color:var(--ink)}
.cta .btn{position:absolute;left:243px;top:14px;border:1px solid var(--blue-dark);color:var(--blue-dark);font-size:6.5px;padding:5px 4px;font-weight:700}
.foot h4{font-size:8.5px;color:#555;font-weight:400;text-transform:uppercase;letter-spacing:.2px}
.foot ul{list-style:none;margin-top:14px}
.foot li{font-size:6.3px;height:13.5px;display:flex;align-items:center;gap:8px;color:var(--text)}
.foot .big{font-size:7px;color:var(--ink);text-transform:uppercase;height:14px}
.hours{font-size:5.6px;margin-top:12px}
.hours div{display:flex;height:11.5px}
.hours b{width:50px;color:var(--ink)}
.contact{font-size:6.3px;margin-top:12px}
.contact div{display:flex;align-items:center;gap:4px;height:12px;color:var(--ink)}
.baseline{left:120px;top:1164px;width:525px;height:1px;background:#ddd}
.copy{left:125px;top:1172px;font-size:5.6px;color:var(--ink)}
.legal{left:367px;top:1171px;font-size:6.3px;display:flex;gap:11px}
.footbrand{left:530px;top:1170px;font-size:10px;font-weight:400;color:#bdbdbd}
</style>
</head>
<body>
<svg width="0" height="0" style="position:absolute">
  <symbol id="user" viewBox="0 0 10 10"><circle cx="5" cy="3" r="2.2" fill="currentColor"/><path d="M1 10c0-3 1.8-4.3 4-4.3S9 7 9 10z" fill="currentColor"/></symbol>
  <symbol id="chev" viewBox="0 0 6 6"><path d="M1.5 0.8L4.3 3 1.5 5.2" fill="none" stroke="currentColor" stroke-width="1.2"/></symbol>
</svg>

<header class="abs topbar">
  <span class="phone"><svg width="8" height="8" viewBox="0 0 10 10"><rect width="10" height="10" rx="1.5" fill="#444"/><path d="M3 2.3c-.6.4-.8 1.3.1 2.8s2 2.5 2.9 2.6c.6 0 1-.4 1.2-.8L6 6c-.3.3-.6.4-.9.1C4.6 5.7 4.3 5.3 4 4.8c-.2-.3 0-.6.3-.8L3.2 2.2z" fill="#fff"/></svg>804-555-0190</span>
  <span class="sep"></span><a>name@ltfhealth.ca</a>
  <span class="right"><a>Book an Appointment</a><a>Physical Toolbox</a></span>
</header>

<div class="abs sheet"></div>
<div class="abs brand">
  <div class="name">LTF Health Centre</div>
  <div class="tag">Family and occupational care</div>
</div>
<nav class="abs nav"><span>Home</span><span>Our Clinic</span><span class="on">Our Staff</span><span>Resources</span><span>Alerts</span><span>Contact Us</span></nav>
<div class="abs rule"></div>
<div class="abs crumbband"><h1>OUR STAFF</h1><p>Home &nbsp;»&nbsp; Our Staff</p></div>

<h2 style="left:128px;top:117px">Our Chief Doctors</h2>
<div class="abs search"><span>Search doctors or specialist</span><i><svg width="7" height="7" viewBox="0 0 10 10"><circle cx="4" cy="4" r="3" fill="none" stroke="#fff" stroke-width="1.6"/><path d="M6.3 6.3L9 9" stroke="#fff" stroke-width="1.8"/></svg></i></div>

<!-- chief doctors -->
<div class="abs avatar" style="left:128px;top:153px;width:74px;height:74px" role="img" aria-label="Portrait of Dr. Liverhand"></div>
<div class="abs card" style="left:210px;top:153px;width:157px">
  <div class="bar"><span class="ico"><svg width="7" height="7" color="#fff"><use href="#user"/></svg></span><b>Liverhand,</b>&nbsp;<span class="deg">MbChB</span></div>
  <p>Saleem naijar kaasram eerie can be disbursed in the wofl like of a fox that is her thing smaoasa lase lemedds laasd pamade eleifend sapien.</p>
  <hr><div class="spec">Gastroenterologist</div><div class="mail">Email: <a>oliver@mailbox.ca</a></div>
</div>
<div class="abs avatar" style="left:376px;top:153px;width:74px;height:74px" role="img" aria-label="Portrait of Dr. Tena Fallow"></div>
<div class="abs card" style="left:459px;top:153px;width:157px">
  <div class="bar"><span class="ico"><svg width="7" height="7" color="#fff"><use href="#user"/></svg></span><b>Tena Fallow,</b>&nbsp;<span class="deg">MPH</span></div>
  <p>Fusce vulputate jala kala ssamsa saleem naijar kaasram eerie can be disbursed in the wofl like of a fox that is her thing.</p>
  <hr><div class="spec">Anesthesiologist</div><div class="mail">Email: <a>tinaf@mailbox.ca</a></div>
</div>
<div class="abs avatar" style="left:128px;top:257px;width:74px;height:74px" role="img" aria-label="Portrait of Dr. Stacy Bekkers"></div>
<div class="abs card" style="left:210px;top:257px;width:157px">
  <div class="bar"><span class="ico"><svg width="7" height="7" color="#fff"><use href="#user"/></svg></span><b>Stacy Bekkers,</b>&nbsp;<span class="deg">MPH</span></div>
  <p>Eerie can be disbursed in the wofl like of a fox that is her thing smaoasa lase lemedds laasd pamade eleifend sapien.</p>
  <hr><div class="spec">Neurosurgeon</div><div class="mail">Email: <a>liver@mailbox.ca</a></div>
</div>
<div class="abs avatar" style="left:376px;top:257px;width:74px;height:74px" role="img" aria-label="Portrait of Dr. Romana Kulunski"></div>
<div class="abs card" style="left:459px;top:257px;width:157px">
  <div class="bar"><span class="ico"><svg width="7" height="7" color="#fff"><use href="#user"/></svg></span><b>Romana Kulunski,</b>&nbsp;<span class="deg">MPH</span></div>
  <p>Naijar kaasram eerie can be disbursed in the wofl like of a fox that is her thing smaoasa lase lemedds laasd pamade eleifend sapien.</p>
  <hr><div class="spec">Opthalmology</div><div class="mail">Email: <a>tinaf@mailbox.ca</a></div>
</div>

<div class="abs divider" style="top:366px"></div>

<!-- specialists -->
<h3 style="left:131px;top:388px">Our Specialists</h3>
<div class="abs avatar" style="left:133px;top:412px;width:41px;height:41px" role="img" aria-label="Portrait of Drew Stronghold"></div>
<div class="abs card" style="left:186px;top:412px;width:184px">
  <div class="bar"><span class="ico"><svg width="7" height="7" color="#fff"><use href="#user"/></svg></span><b>Drew Stronghold,</b>&nbsp;<span class="deg">MPH</span><em>Public Health</em></div>
  <p>Fusce vulputate jala kala ssamsa lase lemedds laasd pamade eleifend sapien.</p>
  <hr><div class="mail">Email: <a>drew@mailbox.ca</a></div>
</div>
<div class="abs avatar" style="left:383px;top:412px;width:41px;height:41px" role="img" aria-label="Portrait of James Linwood"></div>
<div class="abs card" style="left:435px;top:412px;width:184px">
  <div class="bar"><span class="ico"><svg width="7" height="7" color="#fff"><use href="#user"/></svg></span><b>James Linwood,</b>&nbsp;<span class="deg">MbChB</span><em>Phychology, Medicine</em></div>
  <p>Laasd pamade eleifend sapien. Vestibulum purus quam, sceler-isque ut, mollis sed, nonummy id, metus kalam ka malalm.</p>
  <hr><div class="mail">Email: <a>james@mailbox.ca</a></div>
</div>
<div class="abs avatar" style="left:133px;top:495px;width:41px;height:41px" role="img" aria-label="Portrait of Danny Shane"></div>
<div class="abs card" style="left:186px;top:495px;width:184px">
  <div class="bar"><span class="ico"><svg width="7" height="7" color="#fff"><use href="#user"/></svg></span><b>Danny Shane,</b>&nbsp;<span class="deg">MbChB</span><em>Medicine, Surgery</em></div>
  <p>Vestibulum purus quam, scelerisque ut, mollis sed, nonummy id, metus kalam ka malalm.</p>
  <hr><div class="mail">Email: <a>danny@mailbox.ca</a></div>
</div>
<div class="abs avatar" style="left:383px;top:495px;width:41px;height:41px" role="img" aria-label="Portrait of Lily Jane"></div>
<div class="abs card" style="left:435px;top:495px;width:184px">
  <div class="bar"><span class="ico"><svg width="7" height="7" color="#fff"><use href="#user"/></svg></span><b>Lily Jane,</b>&nbsp;<span class="deg">NSP</span><em>Medicine, Surgery</em></div>
  <p>Vestibulum purus quam, scelerisque ut, mollis sed, nonummy id, metus kalam ka malalm.</p>
  <hr><div class="mail">Email: <a>lily@mailbox.ca</a></div>
</div>

<div class="abs divider" style="top:588px"></div>

<!-- physicians -->
<h3 style="left:129px;top:601px">Physicians List</h3>
<table>
  <thead><tr><th style="width:131px">Doctors Name</th><th style="width:55px">Code</th><th style="width:111px">Department</th><th style="width:83px">Extension Number</th><th>Appointment</th></tr></thead>
  <tbody>
    <tr><td class="doc"><svg width="6" height="6"><use href="#user"/></svg>Jonas Horley</td><td>S005</td><td>Blood Bank</td><td>2231</td><td><span class="fix">FIX APPOINTMENT</span></td></tr>
    <tr><td class="doc"><svg width="6" height="6"><use href="#user"/></svg>Steve Bucanan</td><td>S001</td><td>Nephrology</td><td>2244</td><td><span class="fix">FIX APPOINTMENT</span></td></tr>
    <tr><td class="doc"><svg width="6" height="6"><use href="#user"/></svg>Dorian Jameson</td><td>S002</td><td>Ophthalmology</td><td>5664</td><td><span class="fix">FIX APPOINTMENT</span></td></tr>
    <tr><td class="doc"><svg width="6" height="6"><use href="#user"/></svg>Mac Horley</td><td>S014</td><td>Oncology</td><td>5562</td><td><span class="fix">FIX APPOINTMENT</span></td></tr>
    <tr><td class="doc"><svg width="6" height="6"><use href="#user"/></svg>Lewis James Stefen</td><td>S016</td><td>Anaesthetist Cardiac</td><td>6544</td><td><span class="fix">FIX APPOINTMENT</span></td></tr>
    <tr><td class="doc"><svg width="6" height="6"><use href="#user"/></svg>Carrie Holm</td><td>S015</td><td>Cardio Thoracic</td><td>1224</td><td><span class="fix">FIX APPOINTMENT</span></td></tr>
    <tr><td class="doc"><svg width="6" height="6"><use href="#user"/></svg>Jamie Gandara</td><td>S020</td><td>Gynaecology</td><td>5694</td><td><span class="fix">FIX APPOINTMENT</span></td></tr>
    <tr><td class="doc"><svg width="6" height="6"><use href="#user"/></svg>Jonas Horley</td><td>S005</td><td>Blood Bank</td><td>2231</td><td><span class="fix">FIX APPOINTMENT</span></td></tr>
    <tr><td class="doc"><svg width="6" height="6"><use href="#user"/></svg>Steve Bucanan</td><td>S001</td><td>Nephrology</td><td>2244</td><td><span class="fix">FIX APPOINTMENT</span></td></tr>
    <tr><td class="doc"><svg width="6" height="6"><use href="#user"/></svg>Dorian Jameson</td><td>S002</td><td>Ophthalmology</td><td>5664</td><td><span class="fix">FIX APPOINTMENT</span></td></tr>
    <tr><td class="doc"><svg width="6" height="6"><use href="#user"/></svg>Mac Horley</td><td>S014</td><td>Oncology</td><td>5562</td><td><span class="fix">FIX APPOINTMENT</span></td></tr>
  </tbody>
</table>
<p class="abs note"><b>Note:</b> Fusce vulputate jala kala ssamsa saleem naijar kaasram eerie can be disbursed in the wofl like of a fox that is her thing smaoasa lase lemedds.</p>

<p class="abs blurb">Fusce vulputate jala kala ssamsa saleem naijar kaasram eerie can be disbursed in the wofl like of a fox that is her thing smaoasa lase lemedds laasd.</p>
<div class="abs cta">
  <svg class="abs" width="350" height="51" viewBox="0 0 350 51"><path d="M0 0H338L350 25.5 338 51H0z" fill="var(--blue-pale)"/><rect width="2" height="51" fill="var(--blue)"/></svg>
  <p>Find this is the right choice of the treatment. Fix an appointment now and meet us at the right time.</p>
  <span class="btn">BOOK AN APPOINTMENT</span>
</div>

<!-- footer -->
<div class="abs foot" style="left:125px;top:1019px">
  <h4>Our Clinic</h4>
  <ul>
    <li style="color:var(--blue)"><svg width="5" height="5" color="#777"><use href="#chev"/></svg>Mission</li>
    <li><svg width="5" height="5" color="#777"><use href="#chev"/></svg>Services</li>
    <li><svg width="5" height="5" color="#777"><use href="#chev"/></svg>Schedules</li>
    <li><svg width="5" height="5" color="#777"><use href="#chev"/></svg>Policies</li>
    <li class="big">Staff</li><li class="big">Alerts</li><li class="big">Contact Us</li>
  </ul>
</div>
<div class="abs foot" style="left:236px;top:1019px">
  <h4>Resources</h4>
  <ul>
    <li style="color:var(--blue)"><svg width="5" height="5" color="#777"><use href="#chev"/></svg>Our Clinic</li>
    <li><svg width="5" height="5" color="#777"><use href="#chev"/></svg>Mission</li>
    <li><svg width="5" height="5" color="#777"><use href="#chev"/></svg>Services</li>
    <li><svg width="5" height="5" color="#777"><use href="#chev"/></svg>Policies</li>
  </ul>
</div>
<div class="abs foot" style="left:343px;top:1019px">
  <h4>Hours of Operation</h4>
  <div class="hours">
    <div><b>Monday</b>09:00 am - 4:00 pm</div>
    <div><b>Tuesday</b>05:00 am - 10:00 pm</div>
    <div><b>Wednesday</b>Not Available</div>
    <div><b>Thursday</b>09:00 am - 4:00 pm</div>
    <div><b>Friday</b>09:00 am - 4:00 pm</div>
    <div><b>Saturday</b>09:00 am - 4:00 pm</div>
    <div><b>Sunday</b>Not Available</div>
    <div style="color:var(--muted);text-decoration:underline">Holiday Hours</div>
  </div>
</div>
<div class="abs foot" style="left:497px;top:1019px">
  <h4>Contact Us</h4>
  <div class="contact">
    <p style="color:var(--text);margin-bottom:8px">418 Birch Street, Vancouver, B.C.<br>Canada, V5K 0R2</p>
    <div><svg width="6" height="6" viewBox="0 0 10 10"><path d="M2 1c-1 .6-1.3 2 .2 4.5S5.6 9 7 9c.8 0 1.4-.5 1.7-1L7 6.4c-.4.4-.9.5-1.3.2-.7-.6-1.2-1.2-1.6-1.9-.3-.5 0-.9.4-1.2L3.4 1z" fill="#666"/></svg><b>Phone :</b> 1604-555-0147</div>
    <div><svg width="6" height="6" viewBox="0 0 10 10"><rect y="2" width="10" height="7" fill="#666"/><path d="M0 2l5 4 5-4" stroke="#fff" fill="none"/></svg><b>Email :</b> <a>info@ltfhealth.ca</a></div>
    <div><svg width="6" height="6" viewBox="0 0 10 10"><circle cx="5" cy="5" r="4.5" fill="#666"/><path d="M1 5h8M5 .5v9" stroke="#fff" stroke-width=".8"/></svg><b>Website :</b> <a>www.ltfhealth.ca</a></div>
  </div>
</div>

<div class="abs baseline"></div>
<p class="abs copy">Copyright © 2015 LTF Health Centre Medical Healthcare Solutions. All Rights Reserved |</p>
<nav class="abs legal"><a>Terms</a><a>Privacy Policy</a><a>Legal Agreement</a></nav>
<div class="abs footbrand">LTF Health Centre</div>
</body>
</html>
```